BOLD & MINIMALIST DESIGN NEEDED

We want a very bold but minimalistic business card design that is impactful and utilizes both sides of the business card. Our current logo is included for your use.

We want bold fonts and good use of negative space. We don't want the logo to overpower the design.

Target Market(s)

Professionals who are building new commercial buildings.

Industry/Entity Type

Construction

Contact Information for Business Card

Name, Title, email, office phone, cell phone, website

Font styles to use
Serif
Sans Serif

Requirements
Must have
• Bold design!

```html
<!DOCTYPE html>
<html lang="en">
<head>
<meta charset="utf-8">
<title>Ridgeway Design + Build – Business Card</title>
<link href="https://fonts.googleapis.com/css2?family=Montserrat:wght@400;500;700;800&display=swap" rel="stylesheet">
<style>
  :root {
    --bg-top: #d4d4d4;
    --bg-bottom: #a2a2a2;
    --card: #1e1e1e;
    --green: #7cc242;
    --green-light: #c9e6a8;
    --white: #ffffff;
    --rule: #55643f;
  }
  * { margin: 0; padding: 0; box-sizing: border-box; }
  html, body { width: 1200px; height: 802px; overflow: hidden; }
  body {
    background: linear-gradient(180deg, var(--bg-top), var(--bg-bottom));
    font-family: "Montserrat", Arial, sans-serif;
    color: var(--white);
  }
  .stage {
    position: relative;
    width: 1200px; height: 802px;
    display: flex; align-items: center; justify-content: center; gap: 44px;
  }
  .card {
    position: relative;
    width: 520px; height: 300px;
    background: var(--card);
    border-radius: 22px;
    overflow: hidden;
    box-shadow: 0 12px 28px rgba(0,0,0,.35);
  }

  /* Front */
  .tab {
    position: absolute; top: 0; right: 58px;
    width: 26px; height: 22px; background: var(--green);
  }
  .person { position: absolute; top: 36px; right: 40px; text-align: right; }
  .person-name {
    font-weight: 700; font-size: 23px; letter-spacing: .5px;
    color: var(--green);
  }
  .person-title { font-size: 13px; font-weight: 500; margin-top: 4px; }

  .brand-small {
    position: absolute; top: 102px; left: 34px;
    display: flex; align-items: center; gap: 10px;
  }
  .brand-mark { width: 16px; height: 16px; background: var(--green); }
  .brand-name {
    font-weight: 800; font-size: 22px; line-height: 1.05; text-transform: uppercase;
    color: var(--white);
  }

  .divider {
    position: absolute; left: 34px; right: 40px; top: 176px;
    height: 1px; background: var(--rule);
  }
  .contacts {
    position: absolute; left: 34px; top: 188px;
    list-style: none; font-size: 13px; font-weight: 500; line-height: 20px;
  }
  .contacts li { display: flex; align-items: center; gap: 8px; }
  .contacts svg { width: 11px; height: 11px; fill: var(--green); flex: none; }

  .band { position: absolute; left: 0; bottom: 0; width: 520px; height: 80px; }
  .website {
    position: absolute; right: 34px; bottom: 14px;
    font-size: 13px; font-weight: 500; color: var(--white);
  }

  /* Back */
  .brand-large {
    position: absolute; inset: 0;
    display: flex; align-items: center; justify-content: center; gap: 16px;
  }
  .brand-large .brand-mark { width: 28px; height: 28px; }
  .brand-large .brand-name { font-size: 40px; }
</style>
</head>
<body>
<main class="stage">
  <section class="card card-front" aria-label="Business card front">
    <div class="tab"></div>
    <div class="person">
      <p class="person-name">DORIAN KELLER</p>
      <p class="person-title">CEO/Founder</p>
    </div>

    <div class="brand-small">
      <span class="brand-mark"></span>
      <p class="brand-name">Ridgeway<br>Design + Build</p>
    </div>

    <div class="divider"></div>

    <ul class="contacts">
      <li><svg viewBox="0 0 12 12"><path d="M2.5 0.8l2 2.2-1 1.4c.7 1.5 1.9 2.7 3.4 3.4l1.4-1 2.2 2-1.2 2.2C5 11 1 7 0.8 2z"/></svg>07 5120 3300</li>
      <li><svg viewBox="0 0 12 12"><path d="M3 0h6v12H3zM4 1.5v8h4v-8z"/></svg>0422 610 945</li>
      <li><svg viewBox="0 0 12 12"><path d="M0 2h12v8H0zM1 3l5 3.5L11 3z"/></svg>info@ridgewaybuild.com</li>
    </ul>

    <svg class="band" viewBox="0 0 520 80" preserveAspectRatio="none" aria-hidden="true">
      <path d="M0 64 L300 64 C316 64 318 42 336 42 L520 42 L520 80 L0 80 Z" fill="var(--green)"/>
      <path d="M0 58 L296 58 C312 58 314 36 332 36 L520 36 L520 38 L334 38 C316 38 314 60 298 60 L0 60 Z" fill="var(--green-light)"/>
      <rect x="0" y="70" width="520" height="3" fill="var(--card)"/>
    </svg>
    <p class="website">www.ridgewaybuild.com</p>
  </section>

  <section class="card card-back" aria-label="Business card back">
    <div class="brand-large">
      <span class="brand-mark"></span>
      <p class="brand-name">Ridgeway<br>Design + Build</p>
    </div>
  </section>
</main>
</body>
</html>
```